Dietitian needs awesome business card

I need a contemporary design that's eye catching but professional.
My card is to given to doctors, specialists and patients alike.
I manage patients with chronic diseases
I have uploaded my logo and current business card, I would also like the other Certified Clinical Nutritionist logo incorporated into the design

Target Market(s)

Doctors, specialists and patients

Industry/Entity Type

Healthcare

Contact Information for Business Card

www.brightfieldnutrition.com.au
Ph: 0427 561 903
Fax: 6457 2183
email: marcus.k.diet@fernmail.com
Space on the back of the card with: Appointment date, Appointment time and appointment location

Font styles to use
Serif

Colors
fbee3e
876aae
ffc214

Requirements
Must have
• My Logo
• Certified Clinical Nutritionist Logo
• My 4 locations - Pinebrook Medical Centre, North Corrin Health, Hollis Medical, Ashcombe Doctors Surgery
Nice to have
• I like the colours in my current business card

```html
<!DOCTYPE html>
<html lang="en">
<head>
<meta charset="utf-8">
<title>Brightfield Nutrition &amp; Dietetics – Business Card</title>
<link rel="stylesheet" href="https://fonts.googleapis.com/css2?family=Philosopher&family=Open+Sans:ital,wght@0,400;0,600;1,400&display=swap">
<style>
  :root {
    --bg: #8a8a8a;
    --card: #ffffff;
    --navy: #24358f;
    --green: #8cc63f;
    --grey-text: #555555;
    --rule: #a9a9a9;
    --badge: #f47b20;
  }
  * { box-sizing: border-box; margin: 0; padding: 0; }
  html, body { width: 1105px; height: 1200px; overflow: hidden; }
  body { background: var(--bg); font-family: "Open Sans", sans-serif; position: relative; }

  .card {
    position: absolute; left: 102px; width: 900px; height: 510px;
    background: var(--card);
  }
  .card--front { top: 52px; }
  .card--back { top: 638px; }

  /* Front */
  .brand {
    position: absolute; left: 0; right: 0; top: 92px;
    display: flex; align-items: center; justify-content: center; gap: 22px;
  }
  .brand__dot { width: 120px; height: 120px; border-radius: 50%; background: var(--green); flex: none; }
  .brand__name {
    font-family: "Philosopher", serif; color: var(--navy);
    font-size: 46px; line-height: 1.1;
  }
  .person {
    position: absolute; right: 468px; top: 296px; text-align: right;
  }
  .person__name { font-family: "Philosopher", serif; color: var(--navy); font-size: 33px; line-height: 40px; }
  .person__role { font-family: "Philosopher", serif; color: var(--green); font-size: 24px; line-height: 34px; }
  .person__email { font-style: italic; color: var(--grey-text); font-size: 21px; line-height: 34px; }
  .divider { position: absolute; left: 452px; top: 303px; width: 1.5px; height: 103px; background: var(--rule); }
  .contacts { position: absolute; left: 480px; top: 305px; list-style: none; }
  .contacts li { display: flex; align-items: center; gap: 12px; height: 35px; color: var(--grey-text); font-size: 23px; }
  .contacts svg { width: 24px; height: 24px; fill: var(--navy); flex: none; }

  /* Back */
  .back-mark { position: absolute; left: 58px; top: 46px; width: 104px; height: 104px; border-radius: 50%; background: var(--green); }
  .cred-badge {
    position: absolute; left: 624px; top: 48px; width: 215px; height: 100px;
    background: var(--badge); border-radius: 4px;
    display: flex; align-items: center; justify-content: space-between; padding: 0 12px 0 12px;
  }
  .cred-badge__text { color: #fff; font-size: 15px; line-height: 19px; }
  .cred-badge__seal { width: 70px; height: 70px; border-radius: 50%; background: #fff; flex: none; }
  .write-line { position: absolute; left: 60px; width: 775px; height: 1.5px; background: var(--rule); }
  .appt { position: absolute; left: 60px; top: 326px; width: 775px; display: flex; align-items: baseline; color: var(--navy); font-family: "Philosopher", serif; font-size: 25px; }
  .appt__fill { border-bottom: 2px dotted var(--navy); height: 1px; margin: 0 8px; align-self: flex-end; margin-bottom: 8px; }
  .appt__fill--date { width: 350px; }
  .appt__fill--time { width: 170px; }
  .appt__ampm { font-family: "Open Sans", sans-serif; font-size: 17px; }
  .locations { position: absolute; left: 60px; top: 396px; width: 780px; display: grid; grid-template-columns: 452px 1fr; row-gap: 6px; list-style: none; }
  .locations li { display: flex; align-items: center; gap: 10px; color: var(--grey-text); font-size: 23px; line-height: 32px; }
  .locations li::before { content: ""; width: 19px; height: 19px; border: 2px solid var(--navy); flex: none; }
</style>
</head>
<body>
  <section class="card card--front">
    <div class="brand">
      <span class="brand__dot"></span>
      <span class="brand__name">Brightfield<br>Nutrition &amp; Dietetics</span>
    </div>
    <div class="person">
      <p class="person__name">Marcus Kellaway</p>
      <p class="person__role">Nutritionist &amp; Chef</p>
      <p class="person__email">marcus.k.diet@fernmail.com</p>
    </div>
    <span class="divider"></span>
    <ul class="contacts">
      <li><svg viewBox="0 0 24 24" aria-hidden="true"><path d="M6.6 10.8a15.1 15.1 0 0 0 6.6 6.6l2.2-2.2a1 1 0 0 1 1-.25 11.4 11.4 0 0 0 3.6.57 1 1 0 0 1 1 1V20a1 1 0 0 1-1 1A17 17 0 0 1 3 4a1 1 0 0 1 1-1h3.5a1 1 0 0 1 1 1c0 1.25.2 2.45.57 3.57a1 1 0 0 1-.25 1z"/></svg>0427 561 903</li>
      <li><svg viewBox="0 0 24 24" aria-hidden="true"><path d="M7 3h10v5H7zM4 9h16a2 2 0 0 1 2 2v6h-4v4H6v-4H2v-6a2 2 0 0 1 2-2zm4 7v3h8v-3z"/></svg>6457 2183</li>
      <li><svg viewBox="0 0 24 24" aria-hidden="true"><path d="M3 5h18v14H3zm2 2v.5l7 4.5 7-4.5V7zm0 2.9V17h14V9.9l-7 4.5z"/></svg>brightfieldnutrition.com.au</li>
    </ul>
  </section>

  <section class="card card--back">
    <span class="back-mark"></span>
    <div class="cred-badge">
      <p class="cred-badge__text">Certified<br>Clinical<br>Nutritionist</p>
      <span class="cred-badge__seal"></span>
    </div>
    <span class="write-line" style="top:201px"></span>
    <span class="write-line" style="top:248px"></span>
    <span class="write-line" style="top:298px"></span>
    <div class="appt">
      <span>Date :</span><span class="appt__fill appt__fill--date"></span>
      <span>Time :</span><span class="appt__fill appt__fill--time"></span>
      <span class="appt__ampm">AM/PM</span>
    </div>
    <ul class="locations">
      <li>Pinebrook Medical Centre</li>
      <li>Ashcombe Doctors Surgery</li>
      <li>North Corrin Health</li>
      <li>Hollis Medical</li>
    </ul>
  </section>
</body>
</html>
```